Matching business card for my website and logo

Hi.
I need a nice business card design that matches with my website and logo.
I'm a freelance software engineer. I focus mainly on businesses. My specialty is the development and management of complex web applications and related technologies. I'm a certified Scrum Master with hands on experience, so I can guide a software project based on agile practises as well.
I hope you can deliver something nice. Looking forward to your designs.
Updates
Here some inspiration for your design process. I really like these styles:www.designcrowd.nl/design/1446967www.designcrowd.nl/design/954677www.designcrowd.com/design/1221776www.designcrowd.nl/design/2521542www.designcrowd.nl/design/4736001en.99designs.nl/stationery-design/contests/create-business-cards-letterhead-envelopes-cyber-security-start-568299/entries/150Good luck! Added Monday, February 22, 2016
Hi designers,Thanks for all your work.Please use the color scheme that my website uses.See the attached website-design.jpg in the brief description for the complete design.I don't use the blue color anymore. The logo files are not updated yet.Thanks! Added Monday, February 22, 2016
Target Market(s)
IT businesses, other general business that require a specialist in software engineering.
Industry/Entity Type
Computer Software
Contact Information for Business Card
Tim Vosberg
professional in web development & agile project management
Mobile: 0647318290
info@lindestroom.nl
www.lindestroom.nl
Requirements
Must have
- The design must match with the colors and style of my website design. See the website-design.jpg file for the color scheme.
- My certifications should be displayed:
- Norvexa Certified Professional
- Professional Teamvane Master
- My skills should be displayed:
- web development & agile project management
- technical screening
Nice to have
- QR code to my website: www.lindestroom.nl
Should not have
- - don't use the blue color in my logo (files are outdated)
- - a font thats to small for people to read

```html
<!DOCTYPE html>
<html lang="en">
<head>
<meta charset="utf-8">
<title>Lindestroom – Business Card</title>
<link href="https://fonts.googleapis.com/css2?family=Open+Sans:wght@400;600&family=Roboto+Condensed:wght@400;700&family=Roboto:wght@400&display=swap" rel="stylesheet">
<style>
  :root {
    --backdrop: #ececec;
    --charcoal: #2b2b2c;
    --brand-red: #b91f24;
    --pattern-red: #b21d22;
    --rule-grey: #8a8a8a;
    --ink-light: #f1f1f1;
    --ink-soft: #dcdcdc;
  }
  * { box-sizing: border-box; margin: 0; padding: 0; }
  html, body {
    width: 1105px; height: 1200px; overflow: hidden;
    background: var(--backdrop);
  }
  .card {
    position: absolute; left: 182px; width: 747px; height: 427px;
  }
  .card--front { top: 119px; background: var(--charcoal); }
  .card--back { top: 637px; background: var(--brand-red); }

  .wordmark {
    position: absolute; left: 52px; top: 56px;
    font: 400 44px/1 "Open Sans", sans-serif;
    letter-spacing: 4px; color: var(--ink-light);
  }
  .tagline {
    position: absolute; left: 54px; top: 116px;
    font: 400 22px/1 "Open Sans", sans-serif; color: var(--ink-light);
  }
  .identity { position: absolute; left: 39px; top: 254px; }
  .identity__name {
    font: 400 32px/1 "Roboto Condensed", sans-serif; color: var(--brand-red);
  }
  .identity__role {
    margin-top: 12px;
    font: 700 19px/28px "Roboto Condensed", sans-serif; color: var(--ink-light);
  }
  .divider {
    position: absolute; left: 313px; top: 254px; width: 1px; height: 97px;
    background: var(--rule-grey);
  }
  .contact { position: absolute; left: 356px; top: 264px; list-style: none; }
  .contact__item {
    display: flex; align-items: center; height: 29px;
    font: 400 20px/1 "Roboto", sans-serif; color: var(--ink-soft);
  }
  .contact__icon { width: 18px; height: 18px; margin-right: 10px; fill: var(--brand-red); }
  .edge-rule {
    position: absolute; left: 0; right: 0; top: 393px; height: 3px; background: #9a9a9a;
  }
  .edge-band {
    position: absolute; left: 0; right: 0; bottom: 0; height: 27px; background: var(--brand-red);
  }

  .back-pattern {
    position: absolute; inset: 0; background: var(--pattern-red);
  }
  .back-mark {
    position: absolute; left: 0; right: 0; top: 50%; transform: translateY(-50%);
    text-align: center;
    font: 400 56px/1 "Open Sans", sans-serif; letter-spacing: 6px; color: #e4e4e8;
  }
</style>
</head>
<body>
  <section class="card card--front">
    <div class="wordmark">LINDESTROOM</div>
    <p class="tagline">Analyze. Design. Build.</p>

    <div class="identity">
      <h1 class="identity__name">Tim Vosberg</h1>
      <p class="identity__role">Developer &amp;<br>Professional Teamvane Master</p>
    </div>

    <div class="divider"></div>

    <ul class="contact">
      <li class="contact__item">
        <svg class="contact__icon" viewBox="0 0 18 18"><path d="M5 0h8a1.5 1.5 0 0 1 1.5 1.5v15A1.5 1.5 0 0 1 13 18H5a1.5 1.5 0 0 1-1.5-1.5v-15A1.5 1.5 0 0 1 5 0zm0.5 2v12h7V2zm3.5 13.2a1 1 0 1 0 0 2 1 1 0 0 0 0-2z"/></svg>
        0647318290
      </li>
      <li class="contact__item">
        <svg class="contact__icon" viewBox="0 0 18 18"><path d="M1 4h16v1.2L9 10 1 5.2zM1 6.8l8 4.8 8-4.8V14H1z"/></svg>
        info@lindestroom.nl
      </li>
      <li class="contact__item">
        <svg class="contact__icon" viewBox="0 0 18 18"><circle cx="9" cy="9" r="8"/><path d="M5 5c2 0 3 1 3 2s-2 1-2 3 2 2 2 4M11 3c0 2 3 2 3 4s-2 2-2 4" stroke="#2b2b2c" stroke-width="1.4" fill="none"/></svg>
        www.lindestroom.nl
      </li>
    </ul>

    <div class="edge-rule"></div>
    <div class="edge-band"></div>
  </section>

  <section class="card card--back">
    <div class="back-pattern" role="img" aria-label="Faint repeating brand pattern on red"></div>
    <div class="back-mark">LINDESTROOM</div>
  </section>
</body>
</html>
```